We need UI/UX design for a public, informational website for The Copper Lantern.
The pages, structure, and content scope are already defined. Designers are required to work only on the UI/UX layout of these existing pages, focusing on clarity, hierarchy, spacing, and usability. Do not add, remove, rename, or reinterpret pages or content.
The website is strictly informational only. It must not include accounts, onboarding, payments, custody, escrow administration, marketplaces, dashboards, or any transactional functionality.
Scope of work
Apply UI/UX design to the predefined website pages
Design layout for text, images, notices, and sections
Ensure consistent components and layout patterns across page types
Optimize layouts for long form, compliance focused content
Content writing, page creation, and branding changes are out of scope.
Structure reference
The complete page list, hierarchy, and content definitions are provided in the technical documentation and must be treated as the primary source of truth.
A Figma link is provided only as a light visual reference for page existence and structure:
https://meadow-knot-48203956.plumsite.example/
Designers must rely on the documentation for in depth and authoritative reference.
Brand guidelines
The Copper Lantern has existing brand guidelines and official logos, including light and dark versions. These assets will be provided and must be followed exactly. Designers must not redesign, alter, or reinterpret the brand identity.
Look and feel direction
The desired visual direction is inspired by:
https://ledgerwaltz.example/
This reference is provided only to indicate:
Institutional and enterprise tone
Clean, modern typography
Strong hierarchy and generous whitespace
Editorial, content first layouts
Do not copy branding, layouts, components, or assets from the reference site.
Hero section direction
The hero section should follow a similar structural approach to the hero used on https://ledgerwaltz.example/
, meaning:
Strong editorial framing
Clear headline hierarchy
Calm, institutional first impression
However, the background video must be Abu Dhabi focused, not generic or global. The video should visually reflect:
Abu Dhabi skyline or architectural language
Institutional, sovereign, long term infrastructure tone
Clean, slow, cinematic motion
No promotional, marketing, or lifestyle visuals
The hero must remain informational, restrained, and credible. No hype. No calls to invest. No implied participation.
Constraints
One global primary CTA only: “Continue to Halvemark” (external)
All other interactions must be informational
No visuals or language implying offers, investment, eligibility, or participation
Clear separation between informational content and any external operational platforms
Deliverables
High fidelity UI/UX designs created in Figma, covering:
Desktop layouts
Tablet layouts where relevant
Mobile layouts
Complete Figma file(s) including:
All designed pages defined in the technical documentation
A reusable component library (headers, footers, cards, notice panels, forms, CTAs, typography styles, spacing system)
Clearly defined layout grids, spacing rules, and text styles
Proper use of components and variants, not detached frames
Designs prepared for developer handoff, including:
Clear layer naming and structure
Auto layout where appropriate
Consistent use of styles and components
Responsive behavior demonstrated within Figma
Notes or annotations only where necessary for clarity
No prototypes, interactions, or motion design beyond basic layout states, unless explicitly requested. The focus is static UI/UX clarity, not animation.
A detailed technical specification document and official brand assets will be provided.
Any designs delivered outside Figma, that alter structure or content, or that ignore the defined constraints, boundaries, or tone will be rejected.

```html
<!DOCTYPE html>
<html lang="en">
<head>
<meta charset="utf-8">
<title>The Copper Lantern — Governance Framework</title>
<link rel="stylesheet" href="https://fonts.googleapis.com/css2?family=Archivo:wght@500;600;700&family=Manrope:wght@400;500;600&family=Sora:wght@600;700;800&display=swap">
<style>
:root{
  --purple:#6a3db0;
  --cyan:#1cc9e2;
  --ink:#1c1c24;
  --body:#4a4a55;
  --muted:#6f6f7a;
  --line:#c9c9d2;
  --footer-bg:#f3f3f5;
  --white:#ffffff;
}
*{margin:0;padding:0;box-sizing:border-box}
html,body{width:1200px;height:3764px;overflow:hidden;background:var(--white)}
body{position:relative;font-family:"Manrope",sans-serif;color:var(--body)}

/* Header */
.site-header{position:absolute;left:0;top:0;width:1200px;height:118px;background:var(--white)}
.brand{position:absolute;left:138px;top:44px;height:28px;display:flex;align-items:center}
.brand-name{font-family:"Manrope",sans-serif;font-weight:600;font-size:19px;color:var(--ink);letter-spacing:.5px;text-transform:uppercase;white-space:nowrap}
.main-nav{position:absolute;top:48px;left:0;width:1200px;font-size:15px;font-weight:500;color:var(--ink)}
.main-nav a{position:absolute;color:inherit;text-decoration:none;white-space:nowrap}
.main-nav a.active{color:var(--purple)}
.main-nav a.active::before{content:"";position:absolute;left:0;right:0;top:-12px;height:3px;background:var(--purple);border-radius:2px}

/* Hero */
.hero{position:absolute;left:0;top:118px;width:1200px;height:560px;
  background:linear-gradient(100deg,rgba(20,35,55,.78) 0%,rgba(40,55,75,.35) 45%,rgba(90,110,120,.15) 100%),
  linear-gradient(180deg,#6d8796 0%,#4d6370 30%,#7b6a55 60%,#3c4e5a 100%)}
.hero-title{position:absolute;left:143px;top:124px;width:520px;font-family:"Sora",sans-serif;font-weight:800;font-size:38px;line-height:48px;color:var(--white);letter-spacing:-.8px}
.hero-lede{position:absolute;left:143px;top:277px;width:500px;font-size:14px;line-height:24px;color:var(--white);font-weight:500}
.cta-primary{position:absolute;left:142px;top:338px;width:231px;height:48px;border-radius:24px;background:linear-gradient(90deg,var(--purple) 0%,var(--cyan) 100%);color:var(--white);font-family:"Sora",sans-serif;font-weight:700;font-size:14px;display:flex;align-items:center;justify-content:center;text-decoration:none}
.slider-btn{position:absolute;top:447px;width:48px;height:48px;border-radius:50%;background:var(--white);display:flex;align-items:center;justify-content:center}

/* Intro */
.intro-dot{position:absolute;left:589px;top:750px;width:22px;height:22px;border-radius:50%;background:linear-gradient(135deg,var(--purple),var(--cyan))}
.intro-title{position:absolute;left:0;top:780px;width:1200px;text-align:center;font-family:"Archivo",sans-serif;font-weight:700;font-size:44px;color:var(--purple);letter-spacing:-1.5px}
.intro-text{position:absolute;left:148px;width:904px;text-align:center;font-size:14.5px;line-height:24px;color:var(--body)}

/* Feature rows */
.timeline{position:absolute;left:598px;top:1150px;height:1540px;border-left:2px dotted #9a9aa6}
.feature-media{position:absolute;left:143px;width:392px;border-radius:38px}
.feature-icon{position:absolute;left:554px;width:90px;height:90px;border-radius:50%;background:var(--white);border:2px solid var(--purple);display:flex;align-items:center;justify-content:center}
.feature-icon::after{content:"";position:absolute;inset:-2px;border-radius:50%;border:2px solid transparent;border-right-color:var(--cyan);border-bottom-color:var(--cyan)}
.feature-body{position:absolute;left:656px;width:400px}
.feature-title{font-family:"Archivo",sans-serif;font-weight:600;font-size:30px;line-height:40px;color:var(--ink);text-transform:uppercase;letter-spacing:-.6px}
.feature-text{margin-top:10px;font-size:14.5px;line-height:24px;color:var(--body);text-align:justify}
.layer-label{margin-top:8px;font-family:"Sora",sans-serif;font-weight:700;font-size:20px;color:var(--purple)}
.layer-text{margin-top:4px;font-size:14.5px;line-height:24px;width:390px}

/* Contact band */
.contact-band{position:absolute;left:0;top:3018px;width:1200px;height:319px;background:linear-gradient(90deg,#6b3fb1 0%,#3e7fcc 50%,#04d0e2 100%);text-align:center;color:var(--white)}
.contact-title{position:absolute;left:0;top:90px;width:1200px;font-family:"Archivo",sans-serif;font-weight:700;font-size:40px;letter-spacing:-1px}
.contact-text{position:absolute;left:240px;top:148px;width:720px;font-size:14.5px;line-height:24px;font-weight:500}

/* Footer */
.site-footer{position:absolute;left:0;top:3337px;width:1200px;height:427px;background:var(--footer-bg)}
.footer-heading{position:absolute;top:90px;font-family:"Sora",sans-serif;font-weight:700;font-size:21px;color:var(--purple)}
.footer-note{position:absolute;left:142px;top:135px;width:400px;font-size:14.5px;line-height:24px;color:var(--ink)}
.footer-links{position:absolute;top:139px;list-style:none;font-size:14.5px;line-height:24px;color:var(--muted)}
.footer-rule{position:absolute;left:143px;top:332px;width:913px;border-top:1px solid var(--line)}
.copyright{position:absolute;left:0;top:352px;width:1200px;text-align:center;font-size:14.5px;color:var(--ink)}
</style>
</head>
<body>

<header class="site-header">
  <div class="brand"><span class="brand-name">The Copper Lantern</span></div>
  <nav class="main-nav">
    <a class="active" style="left:432px">Home</a>
    <a style="left:507px">Framework</a>
    <a style="left:624px">Projects</a>
    <a style="left:717px">Halvemark</a>
    <a style="left:818px">Insights</a>
    <a style="left:907px">Company</a>
    <a style="left:1009px">Contact</a>
  </nav>
</header>

<section class="hero" role="img" aria-label="Aerial view of the Abu Dhabi skyline, towers and coastline">
  <h1 class="hero-title">A Governance Framework for Structured Project Oversight</h1>
  <p class="hero-lede">Clear boundaries. Institutional discipline. Transparent structures for managing risk and accountability.</p>
  <a class="cta-primary" href="#">Continue to Halvemark</a>
  <span class="slider-btn" style="left:952px"><svg width="14" height="14" viewBox="0 0 14 14"><path d="M9 2 4 7l5 5" fill="none" stroke="#1c1c24" stroke-width="2"/></svg></span>
  <span class="slider-btn" style="left:1008px"><svg width="14" height="14" viewBox="0 0 14 14"><path d="M5 2l5 5-5 5" fill="none" stroke="#1c1c24" stroke-width="2"/></svg></span>
</section>

<span class="intro-dot"></span>
<h2 class="intro-title">THE COPPER LANTERN</h2>
<p class="intro-text" style="top:844px">The Copper Lantern is a governance and project origination group. Its purpose is to define structural standards and oversight principles for complex initiatives that may involve multiple parties, staged execution, and long-term accountability. This website publishes those standards and explains how responsibilities are separated across governance, operations, and project-level execution.</p>
<p class="intro-text" style="top:964px">This site is informational. It does not provide onboarding, account access, eligibility checks, custody of funds, escrow administration, or transaction execution. Where operational workflows exist, they are provided through a separate operating platform under separate terms and policies.</p>

<div class="timeline"></div>

<div class="feature-media" style="top:1079px;height:281px;background:linear-gradient(135deg,#e6e8ec,#9fa6b0 60%,#3f4652)" role="img" aria-label="Business meeting with colleagues shaking hands at a table"></div>
<div class="feature-icon" style="top:1079px"><svg width="50" height="50" viewBox="0 0 50 50" fill="none" stroke="#6a3db0" stroke-width="2"><path d="M8 18 25 8l17 10H8Z"/><path d="M12 20v16M20 20v16M30 20v16M38 20v16M6 40h38M8 36h34"/></svg></div>
<div class="feature-body" style="top:1079px">
  <h3 class="feature-title">Governance and<br>Project Origination</h3>
  <p class="feature-text">Governance in this context refers to the standards that determine how projects are structured and how oversight is described. Origination refers to the initial design and definition of an initiative, including role separation, reporting expectations, and boundary setting before execution begins. The Copper Lantern focuses on these governance-level elements rather than on operating day-to-day workflows.</p>
</div>

<div class="feature-media" style="top:1422px;height:281px;background:linear-gradient(135deg,#1f3a33,#3e5a4d 55%,#c98a3a)" role="img" aria-label="Open hand beneath glowing business icons beside a laptop"></div>
<div class="feature-icon" style="top:1422px"><svg width="50" height="50" viewBox="0 0 50 50" fill="none" stroke="#6a3db0" stroke-width="2"><circle cx="24" cy="27" r="15"/><path d="M9 27h30M24 12c-6 8-6 22 0 30M24 12c6 8 6 22 0 30"/><path d="M34 14c2-6 8-6 10-6-1 5-4 9-10 8" stroke="#1cc9e2"/></svg></div>
<div class="feature-body" style="top:1422px">
  <h3 class="feature-title">Clear Role<br>Separation</h3>
  <p class="feature-text">The ecosystem is designed around clear separation of responsibilities. Governance activities belong at the framework layer. Operational workflows, where available, belong on a separate operating platform designed for process execution and recordkeeping. Assets and project execution, where applicable, belong at the project level through ring-fenced structures created for specific initiatives. This separation is intended to reduce ambiguity and help stakeholders understand who is responsible for what.</p>
</div>

<div class="feature-media" style="top:1806px;height:401px;background:radial-gradient(circle at 50% 45%,#9fd6e6 0%,#3b6f88 35%,#0d1b2a 75%)" role="img" aria-label="Hand holding a glowing sphere with a young plant inside"></div>
<div class="feature-icon" style="top:1806px"><svg width="50" height="50" viewBox="0 0 50 50" fill="none" stroke="#6a3db0" stroke-width="2"><path d="M25 8 40 17v16L25 42 10 33V17Z"/><circle cx="25" cy="25" r="6" stroke="#1cc9e2"/><path d="M25 8v11M25 31v11M10 17l10 5M40 17l-10 5M10 33l10-5M40 33l-10-5"/></svg></div>
<div class="feature-body" style="top:1806px">
  <h3 class="feature-title">How the Ecosystem<br>Works</h3>
  <p class="feature-text" style="text-align:left">At a high level, the ecosystem can be understood as three layers:</p>
  <p class="layer-label">Governance:</p>
  <p class="layer-text">Defines standards, explains role boundaries, and publishes framework information.</p>
  <p class="layer-label">Operations:</p>
  <p class="layer-text">Manages workflow processes such as documentation steps and record-anchored audit</p>
  <p class="layer-label">Project execution:</p>
  <p class="layer-text">Occurs at the project level through dedicated structures that hold responsibilities</p>
</div>

<div class="feature-media" style="top:2309px;height:283px;background:linear-gradient(135deg,#d9d4cc,#8c7f70 55%,#3a3630)" role="img" aria-label="Person signing a document on a desk with small house models"></div>
<div class="feature-icon" style="top:2309px"><svg width="50" height="50" viewBox="0 0 50 50" fill="none" stroke="#6a3db0" stroke-width="2"><rect x="10" y="12" width="28" height="22" rx="2"/><path d="M6 38h38"/><path d="M18 26l6-6 6 6v6H18Z" stroke="#1cc9e2"/></svg></div>
<div class="feature-body" style="top:2309px">
  <h3 class="feature-title">Independent Escrow<br>&amp; Milestone Oversight</h3>
  <p class="feature-text">Some initiatives use independent escrow arrangements to coordinate staged releases linked to milestone completion. Escrow can support execution discipline by requiring defined evidence before releases occur. Escrow does not guarantee outcomes, timelines, or success, and it is not administered by this website operator. This site describes the concept for clarity and transparency.</p>
</div>

<div class="feature-media" style="top:2686px;height:234px;background:linear-gradient(135deg,#e4e6ea,#8e98a4 55%,#2f3844)" role="img" aria-label="Colleagues greeting each other in a bright office"></div>
<div class="feature-icon" style="top:2686px"><svg width="50" height="50" viewBox="0 0 50 50" fill="none" stroke="#6a3db0" stroke-width="2"><circle cx="25" cy="25" r="6" stroke="#1cc9e2"/><path d="M25 9v5M25 36v5M9 25h5M36 25h5M13.7 13.7l3.5 3.5M32.8 32.8l3.5 3.5M13.7 36.3l3.5-3.5M32.8 17.2l3.5-3.5"/><circle cx="25" cy="25" r="12"/></svg></div>
<div class="feature-body" style="top:2686px">
  <h3 class="feature-title">Where Operational<br>Workflows Happen</h3>
  <p class="feature-text">Operational workflows, including any onboarding or workflow participation where permitted, occur on a separate operating platform under separate terms and policies. If you need operational access, use the Halvemark page on this site to navigate externally. This website does not host those workflows.</p>
</div>

<section class="contact-band">
  <h2 class="contact-title">CONTACT AND INQUIRIES</h2>
  <p class="contact-text">If you have questions about governance framework concepts, role boundaries, or information published on this website, you can contact the team using the Contact page. Do not submit sensitive personal data through public forms.</p>
</section>

<footer class="site-footer">
  <h4 class="footer-heading" style="left:140px">Informational notice</h4>
  <p class="footer-note">This website is provided for general informational purposes only. Nothing on this site is an offer, solicitation, or professional advice.</p>
  <h4 class="footer-heading" style="left:655px">Links</h4>
  <ul class="footer-links" style="left:655px">
    <li>Framework</li><li>Projects</li><li>Halvemark</li><li>Insights</li><li>Company</li><li>Contact</li>
  </ul>
  <h4 class="footer-heading" style="left:887px">Legal</h4>
  <ul class="footer-links" style="left:887px">
    <li>Legal (Index)</li><li>Terms of Use</li><li>Privacy Policy</li><li>Cookie Policy</li><li>Disclaimer &amp; Risk Notices</li><li>Acceptable Use Policy</li><li>Accessibility Statement</li>
  </ul>
  <div class="footer-rule"></div>
  <p class="copyright">©&nbsp; Copyrights 2026 | All Rights Reserved</p>
</footer>

</body>
</html>
```